Business Card for a New Zealand IT Startup

I need a business card for VELTA Holdings. We are a young startup based in New Zealand working in internet marketing and web development. The design should have some element connected to New Zealand, such as wave, koru or silver fern, just don't use a kiwi bird.

```html
<!DOCTYPE html>
<html lang="en">
<head>
<meta charset="utf-8">
<title>VELTA Holdings – Business Card</title>
<link href="https://fonts.googleapis.com/css2?family=Open+Sans:wght@400;600;700&display=swap" rel="stylesheet">
<style>
  :root {
    --bg: #e6e6e6;
    --blue: #1271b9;
    --orange: #d0592a;
    --ink: #3a3a3a;
    --paper: #fbfbfb;
  }
  * { margin: 0; padding: 0; box-sizing: border-box; }
  html, body { width: 1200px; height: 852px; overflow: hidden; }
  body {
    background: var(--bg);
    font-family: "Open Sans", Arial, sans-serif;
    position: relative;
  }
  .card {
    position: absolute;
    top: 276px;
    width: 520px;
    height: 300px;
    border-radius: 22px;
    overflow: hidden;
  }
  .card-front {
    left: 50px;
    background: linear-gradient(35deg, var(--orange) 0%, #8a5e5e 38%, #4a6a95 62%, var(--blue) 100%);
  }
  .front-glow {
    position: absolute;
    right: -40px; top: -50px;
    width: 280px; height: 280px;
    border-radius: 50%;
    background: rgba(255, 255, 255, 0.08);
  }
  .wave {
    position: absolute;
    left: 0; width: 100%;
    pointer-events: none;
  }
  .front-wave { bottom: 0; height: 90px; }
  .card-front .wordmark {
    position: absolute;
    left: 0; right: 0; top: 122px;
    text-align: center;
    color: #ffffff;
    font-weight: 700;
    font-size: 44px;
    letter-spacing: 2px;
    line-height: 56px;
  }
  .card-back {
    left: 630px;
    background: var(--paper);
  }
  .card-back .wordmark {
    position: absolute;
    left: 0; right: 0; top: 46px;
    text-align: center;
    color: var(--blue);
    font-weight: 700;
    font-size: 32px;
    letter-spacing: 1.5px;
    line-height: 44px;
  }
  .back-wave-top { top: 100px; height: 24px; }
  .back-wave-bottom { bottom: 22px; height: 24px; }
  .person {
    position: absolute;
    left: 30px; top: 160px;
    width: 200px;
    text-align: right;
  }
  .person-name { color: var(--blue); font-weight: 700; font-size: 20px; line-height: 26px; }
  .person-role { color: var(--ink); font-size: 11px; margin-top: 2px; }
  .contacts {
    position: absolute;
    left: 262px; top: 140px;
    list-style: none;
    font-size: 12.5px;
    color: var(--ink);
  }
  .contacts li { display: flex; align-items: center; gap: 10px; height: 20px; white-space: nowrap; }
  .contacts svg { width: 13px; height: 13px; fill: var(--orange); flex: none; }
  .address {
    position: absolute;
    left: 0; right: 0; bottom: 56px;
    text-align: center;
    font-size: 13px;
    color: var(--ink);
  }
</style>
</head>
<body>
  <section class="card card-front">
    <div class="front-glow"></div>
    <svg class="wave front-wave" viewBox="0 0 520 90" preserveAspectRatio="none" aria-hidden="true">
      <path d="M0 60 C 90 30, 170 30, 260 55 S 430 85, 520 45 L520 90 L0 90 Z" fill="rgba(255,255,255,0.07)"/>
      <path d="M0 60 C 90 30, 170 30, 260 55 S 430 85, 520 45" fill="none" stroke="rgba(255,255,255,0.25)" stroke-width="1.5"/>
    </svg>
    <div class="wordmark">VELTA Holdings</div>
  </section>

  <section class="card card-back">
    <div class="wordmark">VELTA Holdings</div>
    <svg class="wave back-wave-top" viewBox="0 0 520 24" preserveAspectRatio="none" aria-hidden="true">
      <path d="M250 14 C 300 4, 340 4, 385 13 S 460 22, 494 10" fill="none" stroke="var(--blue)" stroke-width="1.6"/>
    </svg>

    <div class="person">
      <div class="person-name">John Doe Smith</div>
      <div class="person-role">Managing Director</div>
    </div>

    <ul class="contacts">
      <li>
        <svg viewBox="0 0 16 16" aria-hidden="true"><path d="M3 1h3l1.5 4-2 1.3a9 9 0 0 0 4.2 4.2L11 8.5l4 1.5v3a2 2 0 0 1-2 2A12 12 0 0 1 1 3a2 2 0 0 1 2-2z"/></svg>
        021-555-0147
      </li>
      <li>
        <svg viewBox="0 0 16 16" aria-hidden="true"><path d="M1 3h14v10H1z M2 4l6 5 6-5" fill="none" stroke="#d0592a" stroke-width="1.6"/></svg>
        hello@veltaholdings.com
      </li>
      <li>
        <svg viewBox="0 0 16 16" aria-hidden="true"><circle cx="8" cy="8" r="7"/><path d="M1 8h14M8 1c3 3 3 11 0 14M8 1c-3 3-3 11 0 14" fill="none" stroke="#fbfbfb" stroke-width="1.1"/></svg>
        www.veltaholdings.com
      </li>
    </ul>

    <div class="address">12 Harbour Lane, Te Aro, Wellington, NZ 6011</div>
    <svg class="wave back-wave-bottom" viewBox="0 0 520 24" preserveAspectRatio="none" aria-hidden="true">
      <path d="M26 10 C 70 20, 110 20, 150 11 S 230 2, 270 14" fill="none" stroke="var(--orange)" stroke-width="1.6"/>
    </svg>
  </section>
</body>
</html>
```